Job Recruiting Agemcy

almost like my current site www.plorvex.com but with these changes see and what i meant about the across the to the site says home job companies categories pages blog and login sign up that should only be the 4 i said only 1 home 2 industries 3 jobs 4 contact us. and remove latest blog post and our partners because that's not us we have to post acuarte information thanks and the name of the company if your using is is work and careful hiring partners and want it easy for us to post and remove jobs and where it emails us every resume or person that applies

Requirements
Must have
• must send email to us when an application is submitted and try to incorparate the colors of current site
Nice to have
• i want a pretty basic site for now just like the one i have but with all thats above were its easy for me being the own to be able to post jobs and everything

```html
<!DOCTYPE html>
<html lang="en">
<head>
<meta charset="utf-8">
<title>Plorvex – Work and Careful Hiring Partners</title>
<link href="https://fonts.googleapis.com/css2?family=Roboto:wght@400;500;700&display=swap" rel="stylesheet">
<style>
:root{
  --purple:#7a2ee8;
  --violet:#6a2fdc;
  --magenta:#b12fc3;
  --nav-active:#9a3ccc;
  --coral:#e8707a;
  --ink:#111111;
  --body:#555555;
  --muted:#666666;
  --white:#ffffff;
  --footer:#000000;
  --btn:linear-gradient(90deg,var(--violet),var(--magenta));
}
*{margin:0;padding:0;box-sizing:border-box}
html,body{width:1200px;height:3633px;overflow:hidden;background:var(--white)}
body{position:relative;font-family:"Roboto",sans-serif;color:var(--ink)}
.abs{position:absolute}
.btn{position:absolute;display:flex;align-items:center;justify-content:center;background:var(--btn);color:var(--white);font-size:15px;font-weight:500;letter-spacing:1.6px;text-transform:uppercase}
.center{left:0;width:1200px;text-align:center}

/* header */
.site-header{position:absolute;left:0;top:0;width:1200px;height:113px;background:var(--white);z-index:3}
.brand-disc{position:absolute;left:49px;top:-20px;width:156px;height:171px;border-radius:0 0 78px 78px;background:var(--white);z-index:4;display:flex;flex-direction:column;align-items:center;justify-content:center;gap:8px}
.brand-disc .mark{width:34px;height:34px;border-radius:50%;background:var(--magenta)}
.brand-disc .name{font-size:20px;font-weight:700;color:var(--violet);letter-spacing:1px}
.nav a{position:absolute;top:48px;font-size:15px;letter-spacing:1.8px;color:#666;text-decoration:none}
.nav a.active{color:var(--nav-active)}

/* hero */
.hero{position:absolute;left:0;top:113px;width:1200px;height:607px;background:linear-gradient(100deg,#8c8c8a 0%,#c8c5c0 35%,#e6e3de 55%,#a7a39d 80%,#4f4d4a 100%)}
.hero-sub{top:305px;font-size:26px;font-weight:500}
.hero-title{top:350px;font-size:44px;font-weight:700;letter-spacing:-.5px}
.field{position:absolute;top:424px;height:41px;background:var(--white);display:flex;align-items:center;padding-left:14px;gap:10px;font-size:16px;color:#777}

/* welcome */
.welcome-art{left:155px;top:825px;width:212px;height:383px;background:linear-gradient(160deg,#e9e6ea,#8b6f66 55%,#c98f4e)}
.welcome-title{left:516px;top:882px;font-size:35px;font-weight:700}
.welcome-copy{left:516px;top:944px;width:560px;font-size:18px;line-height:33px;color:var(--body)}

/* industries */
.industries{left:0;top:1318px;width:1200px;height:511px;background:linear-gradient(180deg,#7a2ee8,#8a2ee6)}
.section-title-light{top:1414px;font-size:35px;font-weight:700;color:var(--white)}
.ind-photo{position:absolute;top:1474px;height:193px}
.ind-caption{position:absolute;top:1678px;width:250px;font-size:16px;font-weight:500;line-height:24px;color:var(--white)}

/* jobs */
.section-title{font-size:35px;font-weight:700}
.job-photo{position:absolute;top:1983px;width:337px;height:225px}
.job-caption{position:absolute;top:2224px;width:337px;font-size:16px;font-weight:500;line-height:26px}

/* cta */
.cta{left:0;top:2456px;width:1200px;height:273px;background:linear-gradient(180deg,#e8707a 0%,#b34fb8 55%,#8536de 100%)}
.cta-title{left:88px;top:2553px;font-size:35px;font-weight:700;color:var(--white)}
.cta-sub{left:88px;top:2607px;font-size:16px;color:var(--white)}
.cta-btn{position:absolute;top:2572px;height:41px;background:var(--white);color:#e0606e;display:flex;align-items:center;justify-content:center;font-size:15px;font-weight:500;letter-spacing:1.6px}

/* testimonials */
.avatar{position:absolute;border-radius:50%}
.quote{top:3050px;font-size:16px;line-height:31px;color:var(--muted)}
.quote-name{top:3128px;font-size:16px}

/* footer */
.site-footer{left:0;top:3253px;width:1200px;height:380px;background:var(--footer);color:var(--white)}
.foot-h{position:absolute;top:3320px;font-size:20px;font-weight:500}
.foot-link{position:absolute;font-size:13px}
.foot-input{position:absolute;left:825px;top:3376px;width:285px;height:44px;border:1px solid var(--white);display:flex;align-items:center;padding-left:20px;font-size:13px}
.copyright{top:3598px;font-size:13px;color:var(--white)}
</style>
</head>
<body>

<header class="site-header">
  <nav class="nav">
    <a class="active" style="left:371px">HOME</a>
    <a style="left:461px">INDUSTRIES</a>
    <a style="left:620px">JOBS</a>
    <a style="left:733px">CONTACT US</a>
  </nav>
  <div class="btn" style="left:907px;top:34px;width:203px;height:46px">Log in/ Sign up</div>
</header>
<div class="brand-disc"><span class="mark"></span><span class="name">PLORVEX</span></div>

<section class="hero" role="img" aria-label="Photo of a recruiter interviewing a candidate at a desk"></section>
<div class="abs center hero-sub">Search from 1000+ job offers</div>
<div class="abs center hero-title">YOUR CAREER STARTS HERE!</div>
<div class="field" style="left:165px;width:323px">
  <svg width="14" height="14" viewBox="0 0 14 14"><circle cx="6" cy="6" r="4.5" fill="none" stroke="#777" stroke-width="2"/><line x1="9.5" y1="9.5" x2="13" y2="13" stroke="#777" stroke-width="2"/></svg>Keywords</div>
<div class="field" style="left:496px;width:323px">
  <svg width="12" height="15" viewBox="0 0 12 15"><path d="M6 1a5 5 0 0 1 5 5c0 4-5 8-5 8S1 10 1 6a5 5 0 0 1 5-5z" fill="#777"/><circle cx="6" cy="6" r="2" fill="#fff"/></svg>Location</div>
<div class="btn" style="left:828px;top:424px;width:208px;height:41px">Search</div>

<div class="abs welcome-art" role="img" aria-label="Office photo of hands working at a desk"></div>
<h2 class="abs welcome-title">WELCOME TO PLORVEX</h2>
<p class="abs welcome-copy">We have over 35 years of Specialized Recruiting and souring experience. We cover a broad spectrum of industries to include some of the top aerospace and pharmaceutical commercial companies of today.</p>
<div class="btn" style="left:516px;top:1103px;width:209px;height:42px">Contact us</div>

<section class="abs industries" role="img" aria-label="Purple tinted photo of office workers"></section>
<h2 class="abs center section-title-light">INDUSTRIES WE SUPPORT</h2>
<div class="ind-photo" style="left:89px;width:251px;background:linear-gradient(180deg,#1b3f79,#7fa6cf 55%,#d9dde2)" role="img" aria-label="Aircraft flying above clouds"></div>
<div class="ind-photo" style="left:347px;width:249px;background:linear-gradient(160deg,#b8bcc2,#7a8797 50%,#4aa3d8)" role="img" aria-label="Pharmaceutical capsule production machine"></div>
<div class="ind-photo" style="left:604px;width:249px;background:linear-gradient(180deg,#0e1320,#1d2c4c 60%,#2a2a2a)" role="img" aria-label="Person holding a small pet"></div>
<div class="ind-photo" style="left:860px;width:250px;background:linear-gradient(180deg,#6d7fb1,#d7a4b2 45%,#9a8e86 70%,#4b4a4a)" role="img" aria-label="Freight truck on a desert road at dusk"></div>
<div class="ind-caption" style="left:89px">Aero Space- Vex Aero Space Controls, Orbiq Kelda Electric</div>
<div class="ind-caption" style="left:347px">Pharmaceutical/ Biotechnology Vita Gen , Lumen cosmetics</div>
<div class="ind-caption" style="left:631px">Medical - Medrin, Curavon</div>
<div class="ind-caption" style="left:860px">Transportation- Holt Trucking, Parcelway</div>

<h2 class="abs center section-title" style="top:1925px">RECENT JOBS</h2>
<div class="job-photo" style="left:89px;background:linear-gradient(135deg,#3a2a20,#7a5a44 50%,#2b2522)" role="img" aria-label="Hands typing on a laptop on a wooden desk"></div>
<div class="job-photo" style="left:431px;background:linear-gradient(135deg,#8a5a3a,#c29a72 50%,#3a4a66)" role="img" aria-label="Team working together at computers"></div>
<div class="job-photo" style="left:773px;background:linear-gradient(135deg,#e8e8e6,#c9c4bd 50%,#8d7f70)" role="img" aria-label="Colleagues in a meeting room with a video screen"></div>
<p class="job-caption" style="left:89px">Lorem ipsum dolor sit amet, consectetur adipiscing elit, sed do eiusmod</p>
<p class="job-caption" style="left:431px">Lorem ipsum dolor sit amet, consectetur adipiscing elit, sed do eiusmod</p>
<p class="job-caption" style="left:773px">Lorem ipsum dolor sit amet, consectetur adipiscing elit, sed do eiusmod</p>
<div class="btn" style="left:529px;top:2310px;width:142px;height:42px">View all</div>

<section class="abs cta" role="img" aria-label="Tinted photo of people standing with documents"></section>
<h2 class="abs cta-title">SEEKING FOR A JOB?</h2>
<p class="abs cta-sub">Browse hundreds of job offers and find the best suitable position.</p>
<div class="cta-btn" style="left:743px;width:179px">SEARCH JOBS</div>
<div class="cta-btn" style="left:930px;width:180px">ADD A RESUME</div>

<h2 class="abs center section-title" style="top:2826px">TESTIMONIALS</h2>
<div class="avatar" style="left:370px;top:2904px;width:120px;height:120px;background:linear-gradient(160deg,#e6e2de,#b7a79a)" role="img" aria-label="Portrait of a client"></div>
<div class="avatar" style="left:525px;top:2888px;width:152px;height:152px;background:linear-gradient(135deg,#e8707a,#8536de);padding:5px">
  <div style="width:142px;height:142px;border-radius:50%;background:var(--white);padding:5px"><div style="width:132px;height:132px;border-radius:50%;background:linear-gradient(160deg,#d9d4ce,#8f7f74)" role="img" aria-label="Portrait of the featured client"></div></div>
</div>
<div class="avatar" style="left:713px;top:2904px;width:120px;height:120px;background:linear-gradient(160deg,#efe9e4,#c9a98e)" role="img" aria-label="Portrait of a client"></div>
<svg class="abs" style="left:77px;top:3071px" width="12" height="18" viewBox="0 0 12 18"><path d="M10 2 3 9l7 7" fill="none" stroke="#444" stroke-width="2.5"/></svg>
<svg class="abs" style="left:1108px;top:3071px" width="12" height="18" viewBox="0 0 12 18"><path d="M2 2l7 7-7 7" fill="none" stroke="#444" stroke-width="2.5"/></svg>
<p class="abs center quote">I didn't even need training. I couldn't have asked for more than this. It really saves me time and effort. Plorvex is exactly what<br>our business has been lacking. I would be lost without Plorvex.</p>
<p class="abs center quote-name">Dana Whitlock HR Manager in Quillstone Inc.</p>

<footer class="abs site-footer"></footer>
<h3 class="foot-h" style="left:90px;color:#fff">Main menu</h3>
<h3 class="foot-h" style="left:313px;color:#fff">Stay In Touch</h3>
<h3 class="foot-h" style="left:563px;color:#fff">Contact Us</h3>
<h3 class="foot-h" style="left:825px;color:#fff">News &amp; updates</h3>
<span class="foot-link" style="left:90px;top:3365px;color:#fff">Home</span>
<span class="foot-link" style="left:90px;top:3395px;color:#fff">Industries</span>
<span class="foot-link" style="left:90px;top:3424px;color:#fff">Jobs</span>
<span class="foot-link" style="left:90px;top:3454px;color:#fff">Contact us</span>
<svg class="abs" style="left:313px;top:3371px" width="130" height="18" viewBox="0 0 130 18">
  <circle cx="7" cy="9" r="6" fill="#fff"/><circle cx="38" cy="9" r="6" fill="#fff"/><circle cx="73" cy="9" r="6" fill="#fff"/>
  <rect x="102" y="3" width="18" height="13" rx="1.5" fill="#fff"/><path d="M102 4l9 7 9-7" fill="none" stroke="#000" stroke-width="1.6"/>
</svg>
<span class="foot-link" style="left:563px;top:3374px;color:#fff">214 Harlow Ave #3 Brookfield,</span>
<span class="foot-link" style="left:563px;top:3401px;color:#fff">OH 44003 USA</span>
<svg class="abs" style="left:563px;top:3429px" width="12" height="12" viewBox="0 0 12 12"><rect width="12" height="12" rx="2" fill="#e8505e"/><path d="M3.5 3c.5 2.5 2.5 5 5 5.5l1-1.3-1.5-.8-.7.7C6 6.5 5.3 5.8 4.8 4.5l.7-.7-.8-1.5z" fill="#fff"/></svg>
<span class="foot-link" style="left:582px;top:3427px;color:#fff">555 010 4827</span>
<svg class="abs" style="left:563px;top:3456px" width="12" height="12" viewBox="0 0 12 12"><rect width="12" height="12" rx="2" fill="#e8505e"/><rect x="2.5" y="3.5" width="7" height="5" fill="none" stroke="#fff"/><path d="M2.5 3.5 6 6.3l3.5-2.8" fill="none" stroke="#fff"/></svg>
<span class="foot-link" style="left:582px;top:3454px;color:#fff">hello@plorvex.com</span>
<div class="foot-input" style="color:#fff">Enter Your Email address</div>
<div class="btn" style="left:825px;top:3436px;width:285px;height:43px">Sign up</div>
<p class="abs center copyright">© Copyrights.2020.The Company Name.All Rights Reserved</p>

</body>
</html>
```